Vantoq Business Card Project showing the logo and a marbo image on the rear

Design a whacky but professional business card, the logo is for the front and the Marbo image is for the rear. Happy to consider other open source Marbo Images if the designer wants to select one from the web. Vantoq is a competitor to OMB.com.au and Pellory.com.au and is based around every property in Australia

Target Market(s)

Business

Contact Information for Business Card

Name, Title, Email, Web, Phone Number

Font styles to use
Other font styles liked:
• avenir

Requirements
Must have
• Image on Back logo on front
Nice to have
• Happy to consider other images on rear, preftably Colin Marbo. Image supplied I own, we can use open source other Marbo Images

```html
<!DOCTYPE html>
<html lang="en">
<head>
<meta charset="utf-8">
<title>Vantoq Business Card</title>
<link rel="stylesheet" href="https://fonts.googleapis.com/css2?family=Rubik:wght@500&family=Roboto:wght@400;700&display=swap">
<style>
  :root {
    --backdrop: #1e1e1e;
    --ink: #0d0d0d;
    --orange: #ef8a12;
    --paper: #f3f3f3;
    --text: #1a1a1a;
    --white: #ffffff;
    --sky-night: #3b3b3d;
    --ground: #8fbf4a;
  }
  html, body {
    margin: 0;
    width: 1200px;
    height: 1138px;
    overflow: hidden;
    background: var(--backdrop);
    font-family: "Roboto", Arial, sans-serif;
  }
  .card {
    position: absolute;
    border-radius: 12px;
    overflow: hidden;
    box-shadow: 0 6px 14px rgba(0,0,0,0.45);
  }
  .card--rear {
    left: 274px; top: 186px; width: 622px; height: 376px;
  }
  .artwork {
    width: 100%; height: 100%;
    background:
      linear-gradient(180deg, rgba(0,0,0,0) 0%, rgba(0,0,0,0) 40%, rgba(230,90,150,0.35) 62%, rgba(120,190,220,0.45) 85%, var(--ground) 100%),
      linear-gradient(90deg, var(--orange) 0%, var(--orange) 49.5%, var(--sky-night) 49.5%, var(--sky-night) 100%);
  }
  .card--front {
    left: 276px; top: 608px; width: 618px; height: 374px;
    background: var(--paper);
  }
  .card__shapes {
    position: absolute; inset: 0;
  }
  .brand {
    position: absolute;
    left: 58px; top: 164px;
    display: flex;
    align-items: center;
    gap: 14px;
    font-weight: 700;
    font-size: 40px;
    line-height: 46px;
    color: var(--white);
    letter-spacing: 0.5px;
  }
  .brand__mark {
    width: 30px; height: 30px;
    background: var(--orange);
    flex: none;
  }
  .contact {
    position: absolute;
    left: 369px; top: 62px;
    color: var(--text);
  }
  .contact__name {
    font-family: "Rubik", Arial, sans-serif;
    font-weight: 500;
    font-size: 25px;
    color: var(--orange);
    margin: 0;
    line-height: 1.2;
  }
  .contact__title {
    font-size: 16px;
    margin: 2px 0 34px;
  }
  .contact__line {
    display: flex;
    align-items: center;
    font-size: 16px;
    height: 23px;
  }
  .contact__icon {
    width: 12px; height: 12px;
    margin: 0 19px 0 7px;
    flex: none;
  }
  .contact__accent { color: var(--orange); }
  .contact__address {
    font-size: 16px;
    line-height: 20px;
    margin-top: 12px;
  }
  .tagline {
    position: absolute;
    left: 304px; top: 312px; width: 314px; height: 38px;
    display: flex; align-items: center; justify-content: center;
    color: var(--white);
    font-size: 16px;
  }
</style>
</head>
<body>
  <div class="card card--rear">
    <div class="artwork" role="img" aria-label="Colourful naive-art city skyline with a train along the bottom, day sky on the left half and night sky on the right half"></div>
  </div>

  <div class="card card--front">
    <svg class="card__shapes" viewBox="0 0 618 374" width="618" height="374">
      <rect x="304" y="312" width="314" height="38" fill="var(--orange)"/>
      <path d="M0,0 H262 C340,90 350,282 284,374 H0 Z" fill="var(--orange)"/>
      <path d="M0,0 H250 C322,88 332,272 244,374 H0 Z" fill="var(--ink)"/>
    </svg>

    <div class="brand"><span class="brand__mark"></span>Vantoq</div>

    <div class="contact">
      <h1 class="contact__name">Dorian Felt</h1>
      <div class="contact__title">Founder &amp; CEO</div>
      <div class="contact__line">
        <svg class="contact__icon" viewBox="0 0 12 12"><circle cx="6" cy="6" r="5.2" fill="none" stroke="var(--orange)" stroke-width="1.2"/><path d="M4,3.5 L5,5.5 L4.6,6 C5,7 5.6,7.4 6.2,7.6 L6.8,7.1 L8.5,8.2" fill="none" stroke="var(--orange)" stroke-width="1.2"/></svg>
        (00) 4817 2096
      </div>
      <div class="contact__line">
        <svg class="contact__icon" viewBox="0 0 12 12"><rect x="0.5" y="2" width="11" height="8" fill="var(--orange)"/><path d="M0.5,2 L6,6.5 L11.5,2" fill="none" stroke="var(--paper)" stroke-width="1"/></svg>
        felt@vantoq.com
      </div>
      <div class="contact__line">
        <svg class="contact__icon" viewBox="0 0 12 12"><circle cx="6" cy="6" r="5.4" fill="var(--orange)"/><path d="M0.6,6 H11.4 M6,0.6 V11.4 M6,0.6 C3,3 3,9 6,11.4 M6,0.6 C9,3 9,9 6,11.4" fill="none" stroke="var(--paper)" stroke-width="0.7"/></svg>
        www.<span class="contact__accent">vantoq</span>.com
      </div>
      <div class="contact__address">Level 4, 18 Carrow Lane,<br>Sydney 2000, Australia</div>
    </div>

    <div class="tagline">Buying, Selling and Research</div>
  </div>
</body>
</html>
```